Thornbury Building Company - Card Design

I am looking to use the logo designs that you already did for me to develop a business card. I would like the card to have a black background and be double sided. I want white and green logo and text. I have attached an inspiration photo of a look that I like. I would like to use the Vertical Logo attached to take up the full front side of the card. On the back where I have my name and information, I would like to have the horizontal logo or maybe even just the image of the 'A' and trees without the text. I am open, but I am looking for something clean and simple and I want the green to really pop! Additional files can be found under Design #: 58302946

Target Market(s)

Homeowners

Industry/Entity Type

Construction

Contact Information for Business Card

Name: Marcus Thornbury, Title: Project Manager, Phone: 555.274.8136, Email: thornburybuildingcompany@mailvesta.com, address: 487 Larkspur Ln, Felton, CA 95033, Lic# 2468317

Colors
00AB8E
00BBA5
67D7C9
C6EFE9
E9F9F6

Requirements
Nice to have
• I would like to see the logos that I have already got from ArtLoomHub, though I am open to new ones

```html
<!DOCTYPE html>
<html lang="en">
<head>
<meta charset="utf-8">
<title>Thornbury Building Company – Business Card</title>
<link href="https://fonts.googleapis.com/css2?family=Arimo:wght@400;700&display=swap" rel="stylesheet">
<style>
  :root {
    --stage: #2a2a2a;
    --card: #141414;
    --card-deep: #0d0d0d;
    --green: #5cbf3f;
    --white: #f4f4f4;
    --muted: #d8d8d8;
    --ghost: #1d1d1d;
  }
  * { box-sizing: border-box; margin: 0; padding: 0; }
  html, body { width: 1200px; height: 801px; overflow: hidden; }
  body {
    background: var(--stage);
    font-family: "Arimo", Arial, sans-serif;
    display: flex;
    align-items: center;
    justify-content: center;
    gap: 40px;
  }
  .card {
    position: relative;
    width: 540px;
    height: 309px;
    background: linear-gradient(135deg, var(--card) 0%, var(--card-deep) 100%);
    border-left: 3px solid var(--green);
    border-bottom: 3px solid var(--green);
    overflow: hidden;
    box-shadow: 0 14px 30px rgba(0,0,0,0.45);
  }
  .brand { display: flex; align-items: center; gap: 12px; }
  .brand-mark { background: var(--green); flex: none; }
  .brand-name { color: var(--white); font-weight: 700; text-transform: uppercase; letter-spacing: 0.06em; line-height: 1.15; }

  /* info side */
  .card-back .brand { position: absolute; left: 34px; top: 30px; }
  .card-back .brand-mark { width: 28px; height: 28px; }
  .card-back .brand-name { font-size: 15px; }
  .ghost-block {
    position: absolute; right: -30px; top: -20px;
    width: 230px; height: 230px;
    background: var(--ghost);
    transform: rotate(12deg);
  }
  .contact { position: absolute; left: 34px; top: 92px; }
  .person-name { color: var(--green); font-weight: 700; font-size: 22px; letter-spacing: 0.03em; text-transform: uppercase; }
  .person-title { color: var(--white); font-size: 13px; margin-top: 3px; }
  .accent-bar { position: absolute; left: 0; top: 100px; width: 14px; height: 30px; background: var(--green); }
  .details { margin-top: 16px; font-size: 12.5px; color: var(--muted); line-height: 1.55; }
  .license { color: var(--green); }
  .reach { margin-top: 12px; }
  .reach-line { display: flex; align-items: center; gap: 8px; }
  .reach-line svg { width: 12px; height: 12px; flex: none; }

  /* logo side */
  .card-front { display: flex; align-items: center; justify-content: center; }
  .card-front .brand { gap: 16px; }
  .card-front .brand-mark { width: 54px; height: 54px; }
  .card-front .brand-name { font-size: 27px; }
</style>
</head>
<body>
  <section class="card card-back" aria-label="Business card, contact side">
    <div class="ghost-block" aria-hidden="true"></div>
    <div class="brand">
      <span class="brand-mark"></span>
      <span class="brand-name">Thornbury<br>Building Company</span>
    </div>
    <span class="accent-bar"></span>
    <div class="contact">
      <p class="person-name">Marcus Thornbury</p>
      <p class="person-title">Project Manager</p>
      <div class="details">
        <p class="license">Lic# 2468317</p>
        <p>487 Larkspur Ln, Felton, CA 95033</p>
        <div class="reach">
          <p class="reach-line">
            <svg viewBox="0 0 12 12" aria-hidden="true"><path fill="#5cbf3f" d="M2.4 0.8l2 2.2-1 1.2c.7 1.5 2 2.8 3.5 3.5l1.2-1 2.2 2-1.2 2.2C4.6 10.6 1.4 7.4.4 2z"/></svg>
            555.274.8136
          </p>
          <p class="reach-line">
            <svg viewBox="0 0 12 12" aria-hidden="true"><rect x="0.5" y="2" width="11" height="8" fill="#5cbf3f"/><path d="M0.8 2.5L6 6.6 11.2 2.5" fill="none" stroke="#141414" stroke-width="1.1"/></svg>
            thornburybuildingcompany@mailvesta.com
          </p>
        </div>
      </div>
    </div>
  </section>

  <section class="card card-front" aria-label="Business card, logo side">
    <div class="brand">
      <span class="brand-mark"></span>
      <span class="brand-name">Thornbury<br>Building Company</span>
    </div>
  </section>
</body>
</html>
```